Business Card - high end, modern health care

Hey designers!

We need a double sided business card for the boutique, cutting edge physical therapy rehabilitation centre in Sydney's Northern Beaches.

With the most qualified physios in the area The Harbourview Motion Clinic does what other physiotherapy practices do not, we take our time with our patients giving them longer appointments, better physios and therefor faster results!

We guarantee that the service people receive at THMC will be unparalleled.

Hence we need a business card to reflect our modern, boutique, high end service. The final design needs to reflect that we are in a class of our own yet with the feel of beachside retreat.

Below I have attached our logo in both blue on white and white on blue. The exact colour is;
and the font that we have used in our logo is Tex Gyre Aventador.

I like the idea of the blue as the main colour as it is more eye catching and our signage onto the main road will be in this blue and in the interest of consistency across marketing the blue needs to be a part of the design. However I would appreciate a few designs onto a wooden background as this is a visual theme within the fitout of the practice.

The design needs to be of standard size (91x55mm).

Target Market(s)

We target people who have an end outcome in mind and those who have had poor experiences with other providers and ensure that everyone gets the care that they deserve with a premium service that is tailored to the individuals circumstances. As a premium service, the target market is highly educated, business and tech savvy with the additional target market of elderly people who have self funded their retirement and see value in paying for the best ongoing rehabilitation to maintain independence.

Industry/Entity Type

Physical Therapy

Contact Information for Business Card

Name, designation( Titled Musculoskeletal Physiotherapist... there will also be those in the company that have multiple designations ie 5 or 6 words long), phone number, email, facebook, instagram, address

Font styles to use
Sans Serif

Colors

Designer to choose colors to be used in the design.

Requirements
Must have
• Front - The logo as large as possible, blue or wooden theme, and all of the important details.
• Back - A blank space/lines on which to write appointment times (no "Appointment, date, time" etc.)
Nice to have
• facebook url
• logos for facebook and instagram
• Mini logos for the phone and email?

```html
<!DOCTYPE html>
<html lang="en">
<head>
<meta charset="utf-8">
<title>The Harbourview Motion Clinic – Business Card</title>
<link href="https://fonts.googleapis.com/css2?family=Montserrat:wght@400;500;800&display=swap" rel="stylesheet">
<style>
  :root {
    --brand-blue: #1a55a6;
    --bright-blue: #2f6fd6;
    --mist: #e3e7f5;
    --ink: #2b2b2b;
    --muted: #555;
    --rule: #555;
    --dash: #b8b8b8;
    --card: #ffffff;
    --backdrop: #2f3846;
    --social-blue: #1d8fd8;
    --social-pink: #e5488f;
  }
  * { margin: 0; padding: 0; box-sizing: border-box; }
  html, body { width: 1200px; height: 1200px; overflow: hidden; }
  body {
    background: var(--backdrop);
    font-family: "Montserrat", sans-serif;
    position: relative;
  }
  .card {
    position: absolute;
    left: 180px;
    width: 840px;
    height: 508px;
    background: var(--card);
    border-radius: 34px;
    overflow: hidden;
  }
  .card--front { top: 62px; }
  .card--back { top: 630px; }

  /* Front */
  .front__halo {
    position: absolute;
    left: 430px; top: 40px;
    width: 380px; height: 380px;
    border-radius: 50%;
    background: var(--mist);
  }
  .front__lockup {
    position: absolute;
    left: 70px; top: 300px;
    display: flex; align-items: center; gap: 16px;
  }
  .front__dot {
    width: 62px; height: 62px; border-radius: 50%;
    background: var(--brand-blue);
    flex: none;
  }
  .front__name {
    color: var(--brand-blue);
    font-weight: 800;
    font-size: 34px;
    line-height: 1.05;
    text-transform: uppercase;
    letter-spacing: 0.5px;
  }

  /* Back */
  .back__mark {
    position: absolute;
    left: 600px; top: 40px;
    width: 200px; height: 200px; border-radius: 50%;
    background: var(--brand-blue);
  }
  .back__rules { position: absolute; inset: 0; }
  .person {
    position: absolute; left: 80px; top: 188px;
  }
  .person__name {
    font-size: 40px; font-weight: 400; color: var(--ink);
  }
  .person__name .accent { color: var(--bright-blue); }
  .person__role {
    font-size: 17px; color: var(--muted); margin-top: 2px; margin-left: 4px;
  }
  .contact {
    position: absolute;
    display: flex; align-items: center; gap: 16px;
    font-size: 20px; color: var(--ink);
    white-space: nowrap;
  }
  .contact svg { flex: none; }
  .contact--phone { left: 80px; top: 300px; }
  .contact--email { left: 80px; top: 342px; }
  .contact--instagram { left: 520px; top: 342px; font-size: 18px; }
  .contact--facebook { left: 120px; top: 420px; font-size: 18px; }
  .social-dot { width: 28px; height: 28px; border-radius: 50%; flex: none; }
  .social-dot--fb { background: var(--social-blue); }
  .social-dot--ig { background: var(--social-pink); }
</style>
</head>
<body>

<section class="card card--front" aria-label="Business card front">
  <div class="front__halo"></div>
  <div class="front__lockup">
    <div class="front__dot"></div>
    <div class="front__name">The Harbourview<br>Motion Clinic</div>
  </div>
</section>

<section class="card card--back" aria-label="Business card back">
  <div class="back__mark"></div>
  <svg class="back__rules" width="840" height="508" viewBox="0 0 840 508">
    <line x1="80" y1="280" x2="560" y2="280" stroke="var(--rule)" stroke-width="1.5"/>
    <line x1="120" y1="396" x2="620" y2="396" stroke="var(--rule)" stroke-width="1.5"/>
    <line x1="80" y1="478" x2="800" y2="478" stroke="var(--dash)" stroke-width="1.5" stroke-dasharray="8 6"/>
  </svg>

  <div class="person">
    <div class="person__name">Name of <span class="accent">Person</span></div>
    <div class="person__role">Designation</div>
  </div>

  <div class="contact contact--phone">
    <svg width="28" height="28" viewBox="0 0 28 28" aria-hidden="true">
      <circle cx="14" cy="14" r="12" fill="none" stroke="#111" stroke-width="2.5"/>
      <path d="M10 8.5c-1 1-1 3 1 6s4 4.5 6 4.5c1 0 2-1 2-1.5l-2-2-1.5 1c-1-.5-2.5-2-3-3l1-1.5-2-2z" fill="#111"/>
    </svg>
    <span>555.018.4420</span>
  </div>
  <div class="contact contact--email">
    <svg width="28" height="22" viewBox="0 0 28 22" aria-hidden="true">
      <rect x="1" y="2" width="26" height="18" fill="#111"/>
      <path d="M1 2l13 10 13-10" fill="none" stroke="#fff" stroke-width="1.6"/>
    </svg>
    <span>hello@harbourviewmotion.com</span>
  </div>
  <div class="contact contact--instagram">
    <div class="social-dot social-dot--ig"></div>
    <span>instagram_name</span>
  </div>
  <div class="contact contact--facebook">
    <div class="social-dot social-dot--fb"></div>
    <span>facebook/name</span>
  </div>
</section>

</body>
</html>
```